A Spin Above Par Company Brochure

I am the owner of a Mobile Disc Jockey company specializing in weddings. I am looking for a Tri Fold color brochure that is modern and eye catching with the focus being on upscale wedding events. I also want it to be easy to read and not overly cluttered ! I would like it to reflect our website located at aspinabovepar.example
I also have different variations and file types of my logo such as jpeg and png files. I need some good dance floor pics. If you do not have any good stock photos I can look through my photo library. I uploaded a logo and pic I found from one of my videos. Not sure if it is worth anything.
We also do Uplighting and Photo Booths which I would like in the brochure. Much of the text copy needed can be taken from our website if needed. Please refer to the website to see what we do and our style.

Target Market(s)

upscale weddings

Industry/Entity Type

wedding dj entertainment & masters of ceremonies

Requirements
Nice to have
• nice pictures of packed dance floors and people having fun

```html
<!DOCTYPE html>
<html lang="en">
<head>
<meta charset="utf-8">
<title>A Spin Above Par – Tri-Fold Brochure</title>
<link rel="stylesheet" href="https://fonts.googleapis.com/css2?family=Roboto+Slab:wght@300;400;600&family=Open+Sans:wght@400;600;700&display=swap">
<style>
:root{
  --stage:#c8c8ca;
  --paper:#efeff1;
  --purple:#7a2284;
  --purple-deep:#5c1868;
  --magenta:#a82a93;
  --red:#d4203c;
  --rose:#d21f5a;
  --ink:#3a3a3f;
  --white:#ffffff;
  --slab:"Roboto Slab", Georgia, serif;
  --sans:"Open Sans", Arial, sans-serif;
}
*{box-sizing:border-box;margin:0;padding:0}
html,body{width:784px;height:1200px;overflow:hidden}
body{background:var(--stage);position:relative;font-family:var(--sans);color:var(--ink)}
.sheet{position:absolute;left:52px;width:680px;height:527px;background:var(--paper);box-shadow:0 8px 10px -4px rgba(0,0,0,.35)}
.sheet--outside{top:41px}
.sheet--inside{top:623px}
.panel{position:absolute;top:0;height:527px;width:227px;overflow:hidden}
.panel--1{left:0}.panel--2{left:227px}.panel--3{left:454px;width:226px}
.panel svg.bg{position:absolute;left:0;top:0}
.abs{position:absolute}
.heading{font-family:var(--slab);font-weight:400;color:var(--red);text-transform:uppercase;font-size:10px;line-height:12px}
.heading .alt{color:var(--purple)}
.copy{font-size:6.6px;line-height:9px;color:var(--ink)}
.copy p+p{margin-top:7px}
.justify{text-align:justify}
.lists{display:flex;gap:24px;left:14px;top:371px}
.lists ul{width:96px}
.lists h4{font-family:var(--slab);font-weight:400;color:var(--red);font-size:7.4px;line-height:10px;margin-bottom:2px}
.lists li{list-style:none;font-size:6.6px;line-height:12.6px;color:var(--ink);padding-left:11px;position:relative;white-space:nowrap}
.lists li::before{content:"";position:absolute;left:0;top:3.6px;width:5px;height:5px;border:1px solid var(--red);border-radius:50%}
.btn{font-family:var(--slab);font-size:9px;text-transform:uppercase;text-align:center;border-radius:10px;line-height:15px}
.btn--outline{border:1.3px solid var(--purple);color:var(--ink);background:var(--white)}
.btn--solid{background:var(--white);color:var(--ink);box-shadow:0 2px 3px rgba(0,0,0,.3)}
.footer{position:absolute;left:0;bottom:0;width:100%;height:27px;background:linear-gradient(90deg,var(--purple-deep),var(--magenta));color:var(--white);font-size:11px;letter-spacing:.4px;text-align:center;line-height:27px;font-weight:600}
.footer--phone{background:linear-gradient(90deg,#c1184b,var(--rose));font-size:12px}
.brand{display:flex;align-items:center;justify-content:center;gap:6px;font-family:var(--slab);font-weight:400;font-size:15px;white-space:nowrap}
.brand .dot{width:16px;height:16px;border:1.5px solid currentColor;border-radius:50%}
.brand--light{color:var(--white)}
.brand--dark{color:#77777d}
.center{text-align:center;width:100%;left:0}
.light-text{color:var(--white)}
.tagline{font-family:var(--slab);font-weight:600;color:var(--purple);text-transform:uppercase;text-align:center;width:100%;left:0}
.services{left:18px;top:99px;width:191px;display:grid;grid-template-columns:repeat(3,1fr);row-gap:11px}
.service{text-align:center;color:var(--white);font-size:5.6px;font-weight:700;line-height:7px;text-transform:uppercase;height:68px}
.service svg{display:block;margin:0 auto 4px}
.url-pill{border:1px solid var(--white);border-radius:10px;color:var(--white);font-size:10px;font-weight:600;letter-spacing:.5px;line-height:16px;padding:0 8px}
</style>
</head>
<body>

<section class="sheet sheet--outside">

  <div class="panel panel--1">
    <svg class="bg" width="227" height="527" viewBox="0 0 227 527">
      <defs>
        <linearGradient id="djDeck" x1="0" y1="0" x2="1" y2="1"><stop offset="0" stop-color="#2a5ab8"/><stop offset=".6" stop-color="#15245a"/><stop offset="1" stop-color="#0a0c22"/></linearGradient>
        <radialGradient id="crowdA"><stop offset="0" stop-color="#c15bc4"/><stop offset="1" stop-color="#3d1349"/></radialGradient>
      </defs>
      <rect width="227" height="527" fill="#efeff1"/>
      <path d="M0 0H227V150Q130 182 0 210Z" fill="url(#djDeck)" role="img" aria-label="Photo of a DJ's hands on a lit mixing deck"/>
      <path d="M0 210Q130 182 227 150" fill="none" stroke="#fff" stroke-width="4"/>
      <circle cx="98" cy="215" r="36" fill="url(#crowdA)" stroke="#fff" stroke-width="3" role="img" aria-label="Photo of guests on a purple-lit dance floor"/>
      <circle cx="160" cy="207" r="40" fill="url(#crowdA)" stroke="#fff" stroke-width="3" role="img" aria-label="Photo of a packed dance floor with raised hands"/>
    </svg>
    <h2 class="heading abs" style="left:14px;top:276px;width:205px">The most recommended DJ's<br>in Southwest Florida</h2>
    <div class="copy abs" style="left:14px;top:302px;width:204px">
      <p>We offer creative ideas and a fresh approach to help you customize your event around the style &amp; vibe that you want. Planning this way is fun and eliminates the stress that comes with preparing for your special day.<br>Are Packed dance floors, personalization, and lots of tired people smiling on their way out at the end of the night how you want your wedding to be remembered?</p>
    </div>
    <div class="lists abs">
      <ul><h4>Weddings</h4><li>Wedding Ceremonies</li><li>DJ Entertainment</li><li>Lighting</li><li>Photo Booth</li><li>Dancing on Clouds</li><li>Monogram Lighting</li></ul>
      <ul><h4>Corporate</h4><li>DJ Entertainment</li><li>Lighting</li><li>Branding</li><li>Photo Booth</li><li>Game Shows</li><li>Karaoke</li></ul>
    </div>
    <div class="btn btn--outline abs" style="left:36px;top:474px;width:156px">Book your event today!</div>
    <div class="footer">www.aspinabovepar.example</div>
  </div>

  <div class="panel panel--2">
    <svg class="bg" width="227" height="527" viewBox="0 0 227 527">
      <defs>
        <linearGradient id="purpleField" x1="0" y1="0" x2="1" y2="1"><stop offset="0" stop-color="#9a2f9a"/><stop offset=".5" stop-color="#7c2385"/><stop offset="1" stop-color="#5f1a6d"/></linearGradient>
        <linearGradient id="ballroom" x1="0" y1="0" x2="0" y2="1"><stop offset="0" stop-color="#5c4a48"/><stop offset="1" stop-color="#2c2426"/></linearGradient>
        <radialGradient id="portrait"><stop offset="0" stop-color="#e7c3a8"/><stop offset="1" stop-color="#8a6a6e"/></radialGradient>
      </defs>
      <rect width="227" height="527" fill="url(#purpleField)"/>
      <path d="M110 200L227 90V300Z" fill="#fff" opacity=".06"/>
      <path d="M0 0H227V165Q120 215 0 235Z" fill="url(#ballroom)" role="img" aria-label="Photo of wedding guests dancing in a ballroom"/>
      <path d="M0 235Q120 215 227 165" fill="none" stroke="#fff" stroke-width="3"/>
      <circle cx="185" cy="178" r="44" fill="url(#portrait)" stroke="#fff" stroke-width="3" role="img" aria-label="Photo of two guests posing with photo booth signs"/>
    </svg>
    <div class="brand brand--light abs center" style="top:236px"><span class="dot"></span>A Spin Above Par</div>
    <p class="abs center light-text" style="top:265px;font-family:var(--slab);font-size:9.5px;line-height:11.5px;text-transform:uppercase">Have your event be remembered<br>as being one of the greats!</p>
    <p class="abs center light-text" style="top:305px;font-size:7.8px;line-height:11px">Weddings, Corporate Events, Private Parties,<br>any event is better with A Spin Above Par</p>
    <p class="abs center light-text" style="top:340px;font-size:7.8px;line-height:11px">Call, text or email us for information and<br>quotes.</p>
    <div class="abs" style="left:95px;top:376px;display:flex;gap:10px"><span style="width:15px;height:15px;border:1px solid #fff;border-radius:50%"></span><span style="width:15px;height:15px;border:1px solid #fff;border-radius:50%"></span></div>
    <div class="btn btn--solid abs" style="left:30px;top:402px;width:166px;line-height:17px">Book your event today!</div>
    <p class="abs center light-text" style="top:430px;font-family:var(--slab);font-size:9.5px">DJ STATION</p>
    <p class="abs center light-text" style="top:445px;font-size:7px;line-height:13px">(555) 014-2290<br>info@aspinabovepar.example<br>www.aspinabovepar.example</p>
    <div class="footer footer--phone">
      <svg width="10" height="10" viewBox="0 0 24 24" style="vertical-align:-1px;margin-right:4px"><circle cx="12" cy="12" r="11" fill="none" stroke="#fff" stroke-width="2"/><path d="M8 6l2 3-1.5 1.5a8 8 0 0 0 5 5L15 14l3 2-1 2.5c-5 0-10-5-10-10Z" fill="#fff"/></svg>555.014.2290
    </div>
  </div>

  <div class="panel panel--3">
    <svg class="bg" width="226" height="527" viewBox="0 0 226 527">
      <defs>
        <linearGradient id="brideDance" x1="0" y1="0" x2="1" y2="1"><stop offset="0" stop-color="#d98bc8"/><stop offset=".5" stop-color="#8d4b7e"/><stop offset="1" stop-color="#3e2a36"/></linearGradient>
      </defs>
      <rect width="226" height="527" fill="#efeff1"/>
      <path d="M0 0H226V60Q110 50 0 115Z" fill="#7a2284"/>
      <path d="M0 115Q110 50 226 60V370Q120 385 0 415Z" fill="url(#brideDance)" role="img" aria-label="Photo of a bride dancing with her guests under pink uplighting"/>
      <path d="M0 115Q110 50 226 60" fill="none" stroke="#fff" stroke-width="5"/>
      <path d="M0 415Q120 385 226 370" fill="none" stroke="#7a2284" stroke-width="5"/>
      <path d="M0 421Q120 391 226 376" fill="none" stroke="#fff" stroke-width="3"/>
    </svg>
    <div class="brand brand--dark abs center" style="top:424px;font-size:16px"><span class="dot"></span>A Spin Above Par</div>
    <p class="tagline abs" style="top:453px;font-size:12.5px;line-height:17px">Modern, tasteful,<br>&amp; fun entertainment</p>
    <div class="footer">www.aspinabovepar.example</div>
  </div>
</section>

<section class="sheet sheet--inside">

  <div class="panel panel--1">
    <svg class="bg" width="227" height="527" viewBox="0 0 227 527">
      <defs>
        <linearGradient id="firstDance" x1="0" y1="0" x2="0" y2="1"><stop offset="0" stop-color="#6a4a3a"/><stop offset=".6" stop-color="#a98a78"/><stop offset="1" stop-color="#f3f1f2"/></linearGradient>
        <linearGradient id="boothGroup" x1="0" y1="0" x2="1" y2="1"><stop offset="0" stop-color="#d9d4d8"/><stop offset="1" stop-color="#6c5e66"/></linearGradient>
      </defs>
      <rect width="227" height="527" fill="#efeff1"/>
      <rect width="227" height="185" fill="url(#firstDance)" role="img" aria-label="Photo of a couple's first dance on a cloud of low fog"/>
      <path d="M0 345H227V527H0Z" fill="url(#boothGroup)" role="img" aria-label="Photo of wedding guests wearing photo booth props"/>
      <path d="M0 470Q110 520 227 490V527H0Z" fill="#7a2284"/>
    </svg>
    <h2 class="heading abs" style="left:14px;top:208px;width:210px">Wedding entertainment planning<br>&amp; coordination <span class="alt">the way you want it</span></h2>
    <div class="copy justify abs" style="left:14px;top:236px;width:206px">
      <p>Beginning with your initial consultation, we listen to you and respond with creative ideas and helpful advice so your event is all about you. We know it's more than just great music, it's keeping you guests engaged and coordinating with your venue and vendors for a smooth and timely event everyone will never forget.</p>
      <p>Contact us now and find out why so many couples continue to place their faith and trust in us to help them create the ultimate wedding experience.</p>
    </div>
  </div>

  <div class="panel panel--2">
    <svg class="bg" width="227" height="527" viewBox="0 0 227 527">
      <defs>
        <linearGradient id="purpleField2" x1="0" y1="0" x2="1" y2="1"><stop offset="0" stop-color="#9a2f9a"/><stop offset=".5" stop-color="#7c2385"/><stop offset="1" stop-color="#5f1a6d"/></linearGradient>
        <radialGradient id="monogram"><stop offset="0" stop-color="#c8a0d6"/><stop offset="1" stop-color="#4a2860"/></radialGradient>
        <radialGradient id="singer"><stop offset="0" stop-color="#c79a88"/><stop offset="1" stop-color="#22182a"/></radialGradient>
      </defs>
      <rect width="227" height="527" fill="url(#purpleField2)"/>
      <path d="M0 300L227 120V380Z" fill="#fff" opacity=".05"/>
      <circle cx="70" cy="475" r="52" fill="url(#monogram)" stroke="#fff" stroke-width="3" role="img" aria-label="Photo of a monogram projected on a dance floor"/>
      <circle cx="150" cy="455" r="58" fill="url(#singer)" stroke="#fff" stroke-width="3" role="img" aria-label="Photo of a guest singing karaoke"/>
    </svg>
    <div class="brand brand--light abs center" style="top:58px;font-size:16px"><span class="dot"></span>A Spin Above Par</div>
    <div class="services abs">
      <div class="service"><svg width="50" height="50" viewBox="0 0 50 50"><circle cx="25" cy="25" r="23.5" fill="none" stroke="#fff" stroke-width="1.5"/><path d="M19 22a6 6 0 1 1 12 0c0 3-3 4-3 7h-6c0-3-3-4-3-7Z" fill="none" stroke="#fff" stroke-width="1.6"/><path d="M22 32h6M22.5 35h5" stroke="#fff" stroke-width="1.6"/></svg>LED Up<br>Lighting</div>
      <div class="service"><svg width="50" height="50" viewBox="0 0 50 50"><circle cx="25" cy="25" r="23.5" fill="none" stroke="#fff" stroke-width="1.5"/><circle cx="29" cy="20" r="5" fill="#fff"/><path d="M26 24L17 35" stroke="#fff" stroke-width="3" stroke-linecap="round"/></svg>Karaoke</div>
      <div class="service"><svg width="50" height="50" viewBox="0 0 50 50"><circle cx="25" cy="25" r="23.5" fill="none" stroke="#fff" stroke-width="1.5"/><path d="M15 30h20a5 5 0 0 0 0-10 7 7 0 0 0-13-1 5 5 0 0 0-7 11Z" fill="none" stroke="#fff" stroke-width="1.5"/></svg>Dancing in<br>the clouds</div>
      <div class="service"><svg width="50" height="50" viewBox="0 0 50 50"><circle cx="25" cy="25" r="23.5" fill="none" stroke="#fff" stroke-width="1.5"/><circle cx="21" cy="27" r="6" fill="none" stroke="#fff" stroke-width="1.6"/><circle cx="29" cy="24" r="6" fill="none" stroke="#fff" stroke-width="1.6"/></svg>Weddings<br>Ceremonies</div>
      <div class="service"><svg width="50" height="50" viewBox="0 0 50 50"><circle cx="25" cy="25" r="23.5" fill="none" stroke="#fff" stroke-width="1.5"/><path d="M17 14h6l-1 9a2 2 0 0 1-4 0ZM27 14h6l-1 9a2 2 0 0 1-4 0ZM20 25v9M30 25v9M17 34h6M27 34h6" fill="none" stroke="#fff" stroke-width="1.5"/></svg>Corporate<br>Events</div>
      <div class="service"><svg width="50" height="50" viewBox="0 0 50 50"><circle cx="25" cy="25" r="23.5" fill="none" stroke="#fff" stroke-width="1.5"/><rect x="16" y="22" width="18" height="13" fill="#fff"/><rect x="15" y="18" width="20" height="4" fill="#fff"/><path d="M25 18v17" stroke="#7c2385" stroke-width="2"/><path d="M25 18c-3-5-7-3-5 0M25 18c3-5 7-3 5 0" fill="none" stroke="#fff" stroke-width="1.5"/></svg>Birthday<br>Parties</div>
      <div class="service"><svg width="50" height="50" viewBox="0 0 50 50"><circle cx="25" cy="25" r="23.5" fill="none" stroke="#fff" stroke-width="1.5"/><path d="M25 14l3.2 7 7.3.6-5.6 4.8 1.8 7.2L25 29.8l-6.7 3.8 1.8-7.2-5.6-4.8 7.3-.6Z" fill="#fff"/></svg>Monogram<br>Lighting</div>
      <div class="service"><svg width="50" height="50" viewBox="0 0 50 50"><circle cx="25" cy="25" r="23.5" fill="none" stroke="#fff" stroke-width="1.5"/><rect x="15" y="19" width="20" height="14" rx="2" fill="none" stroke="#fff" stroke-width="1.6"/><circle cx="25" cy="26" r="4" fill="none" stroke="#fff" stroke-width="1.6"/><rect x="21" y="16" width="8" height="3" fill="#fff"/></svg>Photo<br>Booth</div>
      <div class="service"><svg width="50" height="50" viewBox="0 0 50 50"><circle cx="25" cy="25" r="23.5" fill="none" stroke="#fff" stroke-width="1.5"/><path d="M16 35l6-14 7 7Z" fill="#fff"/><path d="M27 20l3-5M30 23l5-2M26 17v-3M32 17l2-2M34 26l2 1" stroke="#fff" stroke-width="1.5" stroke-linecap="round"/></svg>Game<br>Shows</div>
    </div>
    <p class="abs center light-text" style="top:337px;font-size:8.4px;line-height:12px">Join Over 1,000 Happy Customers that<br>have enjoyed A Spin Above Par</p>
  </div>

  <div class="panel panel--3">
    <svg class="bg" width="226" height="527" viewBox="0 0 226 527">
      <defs>
        <linearGradient id="partyGuests" x1="0" y1="0" x2="0" y2="1"><stop offset="0" stop-color="#5b4a48"/><stop offset=".7" stop-color="#c9b0a4"/><stop offset="1" stop-color="#efeff1"/></linearGradient>
        <linearGradient id="venueRoom" x1="0" y1="0" x2="0" y2="1"><stop offset="0" stop-color="#3a2a5a"/><stop offset="1" stop-color="#7a4aa8"/></linearGradient>
      </defs>
      <rect width="226" height="527" fill="#efeff1"/>
      <rect width="226" height="205" fill="url(#partyGuests)" role="img" aria-label="Photo of laughing party guests with a mustache prop"/>
      <path d="M0 395Q110 350 226 380V527H0Z" fill="url(#venueRoom)" role="img" aria-label="Photo of a reception hall with purple uplighting"/>
      <path d="M0 395Q110 350 226 380" fill="none" stroke="#7a2284" stroke-width="6"/>
      <path d="M0 401Q110 356 226 386" fill="none" stroke="#fff" stroke-width="2"/>
    </svg>
    <h2 class="heading abs" style="left:14px;top:222px">Corporate events</h2>
    <div class="copy justify abs" style="left:14px;top:240px;width:200px">
      <p>With over 30+ years of experience providing DJ entertainment and lighting services for corporate events and company parties, we understand how important creating the right atmosphere and delivering quality entertainment is to the success of your event.</p>
      <p>So whether you're planning a sales incentive meeting, awards presentation, beach party, holiday party or gala evening, let us help you create an event your employees will never forget.</p>
    </div>
    <div class="url-pill abs" style="left:34px;top:499px">www.aspinabovepar.example</div>
  </div>
</section>

</body>
</html>
```